Bright Step Path Flyer, eyecatching

Hi,
To give you an idea of the business for design purposes, #BrighttStepPath is predominantly a recruitment and people development business, ran by me dedicated to training & assisting others in achieving extra income (pt or f/t) around their current commitments, people also have the opportunity to build their own business brand with my support. My brand colours are Red, White and Black, and I would like to incorporate the following text;

#BrightStepPath

Recruiting now! Start today & start earning!

Would you like an extra income, for…
A holiday?…A new car?…Lifestyle changes?
(Can you put a tick box or something similar adjacent to each)

Are you facing…
Redundancy? Birth of a new child? Hefty bills?

If so, I have the solution.

Contact Yvonne Darcott today: (can you insert the appropriate icon for each of the contact details)
Tel: 07419 604172
Twitter: @Bright_StepPath
Email: Yvonne@brightsteppath-example.co.uk
Facebook: www.socialhub-example.com/yvonbrightsteppath

Target Market(s)

Women aged 25-45 years, possibly busy mums too, wanting to earn additinal income to allow them more choices, be it family time, money, new challenge, meeting new people, personal development

Industry/Entity Type

Health And Wellness

Font styles to use
Serif
Sans Serif
Decorative
Script

Colors
ec1f27
ffffff
000000

Requirements
Must have
• My heels logo, be clear concise and eye catching, I also have the following strap line if you wish to use;
• Empowering other to achieve
• Also I have attached a closeup picture of myself but would ideally only like half my face to appear (leftside) similar to the other picture posted - if you can
Nice to have
• Perhaps adding other forms of graphics, or the 3rd picture I have attached with myself...possibly just the shoes though
Should not have
• Too many colours

```html
<!DOCTYPE html>
<html lang="en">
<head>
<meta charset="utf-8">
<title>Bright Step Path – Recruiting Flyer</title>
<link rel="stylesheet" href="https://fonts.googleapis.com/css2?family=Open+Sans:wght@700&family=Playfair+Display:wght@700;900&family=Roboto+Slab:wght@700&display=swap">
<style>
  :root {
    --brand-red: #c30d17;
    --brand-black: #0d0b0c;
    --brand-white: #ffffff;
    --stage: #e4e4e6;
    --photo-dark: #3a3a3c;
    --photo-light: #b9b3b1;
  }
  * { margin: 0; padding: 0; box-sizing: border-box; }
  html, body {
    width: 1200px; height: 1170px; overflow: hidden;
    background: var(--stage);
  }
  .flyer {
    position: absolute; left: 188px; top: 0;
    width: 824px; height: 1170px;
    background: var(--brand-white);
  }
  .flyer svg { display: block; }
  .serif-display { font-family: "Playfair Display", Georgia, serif; }
  .slab { font-family: "Roboto Slab", Georgia, serif; }
  .sans { font-family: "Open Sans", Arial, sans-serif; }
</style>
</head>
<body>
<main class="flyer">
  <svg width="824" height="1170" viewBox="0 0 824 1170">
    <defs>
      <linearGradient id="photoPortraitSide" x1="0" y1="0" x2="1" y2="1">
        <stop offset="0" stop-color="#7d7d7f"/>
        <stop offset="0.5" stop-color="var(--photo-dark)"/>
        <stop offset="1" stop-color="#151515"/>
      </linearGradient>
      <linearGradient id="photoPortraitClose" x1="0" y1="0" x2="1" y2="1">
        <stop offset="0" stop-color="#d9d6d5"/>
        <stop offset="0.6" stop-color="var(--photo-light)"/>
        <stop offset="1" stop-color="#4a4040"/>
      </linearGradient>
    </defs>

    <!-- dark lower panel with curved edge -->
    <path class="panel-dark" d="M0 483 H484 V290 C640 300 760 380 824 497 V1170 H0 Z" fill="var(--brand-black)"/>

    <!-- portrait photos -->
    <rect class="photo photo-side" x="20" y="20" width="215" height="445" rx="5" fill="url(#photoPortraitSide)" role="img" aria-label="Portrait of the business owner in profile"/>
    <rect class="photo photo-close" x="250" y="20" width="215" height="445" rx="5" fill="url(#photoPortraitClose)" role="img" aria-label="Close-up portrait showing half of the owner's face"/>

    <!-- brand mark -->
    <g class="brand-mark">
      <circle cx="242" cy="241" r="150" fill="var(--brand-white)"/>
      <text class="serif-display" x="242" y="251" text-anchor="middle" font-size="30" font-weight="700" fill="var(--brand-black)">Bright Step Path</text>
    </g>

    <!-- hashtag -->
    <text class="serif-display hashtag" x="478" y="256" font-size="35" font-weight="900" fill="var(--brand-black)" textLength="318" lengthAdjust="spacingAndGlyphs">#BrightStepPath</text>

    <!-- headline -->
    <text class="serif-display headline" x="96" y="600" font-size="74" font-weight="900" fill="var(--brand-red)" textLength="635" lengthAdjust="spacingAndGlyphs">RECRUITING NOW!</text>
    <text class="slab subheadline" x="96" y="646" font-size="44" font-weight="700" fill="var(--brand-white)" textLength="635" lengthAdjust="spacingAndGlyphs">START TODAY &amp; START EARNING!</text>

    <!-- question columns -->
    <g class="sans" font-weight="700" font-size="19" fill="var(--brand-white)">
      <text x="132" y="714">WOULD YOU LIKE AN</text>
      <text x="132" y="734">EXTRA INCOME, FOR...</text>
      <text x="469" y="727">ARE YOU FACING...</text>
    </g>
    <line class="column-divider" x1="396" y1="700" x2="396" y2="928" stroke="var(--brand-red)" stroke-width="2"/>

    <!-- option pills -->
    <g class="options sans" font-weight="700" font-size="19" fill="var(--brand-red)">
      <g class="option">
        <rect x="133" y="763" width="225" height="28" rx="10" fill="var(--brand-white)" stroke="var(--brand-red)" stroke-dasharray="3 2"/>
        <circle cx="173" cy="777" r="21" fill="var(--brand-white)" stroke="var(--brand-red)"/>
        <path d="M163 777 l7 7 l13 -14" fill="none" stroke="var(--brand-black)" stroke-width="3"/>
        <text x="219" y="784">A HOLIDAY?</text>
      </g>
      <g class="option">
        <rect x="133" y="827" width="225" height="28" rx="10" fill="var(--brand-white)" stroke="var(--brand-red)" stroke-dasharray="3 2"/>
        <circle cx="173" cy="841" r="21" fill="var(--brand-white)" stroke="var(--brand-red)"/>
        <path d="M163 841 l7 7 l13 -14" fill="none" stroke="var(--brand-black)" stroke-width="3"/>
        <text x="219" y="848">A NEW CAR?</text>
      </g>
      <g class="option">
        <rect x="133" y="890" width="225" height="38" rx="12" fill="var(--brand-white)" stroke="var(--brand-red)" stroke-dasharray="3 2"/>
        <circle cx="173" cy="909" r="21" fill="var(--brand-white)" stroke="var(--brand-red)"/>
        <path d="M163 909 l7 7 l13 -14" fill="none" stroke="var(--brand-black)" stroke-width="3"/>
        <text x="219" y="906" font-size="18">LIFESTYLE</text>
        <text x="219" y="925" font-size="18">CHANGES?</text>
      </g>
      <g class="option">
        <rect x="434" y="763" width="259" height="28" rx="10" fill="var(--brand-white)" stroke="var(--brand-red)" stroke-dasharray="3 2"/>
        <circle cx="474" cy="777" r="21" fill="var(--brand-white)" stroke="var(--brand-red)"/>
        <path d="M464 777 l7 7 l13 -14" fill="none" stroke="var(--brand-black)" stroke-width="3"/>
        <text x="514" y="784">REDUNDANCY?</text>
      </g>
      <g class="option">
        <rect x="434" y="827" width="259" height="28" rx="10" fill="var(--brand-white)" stroke="var(--brand-red)" stroke-dasharray="3 2"/>
        <circle cx="474" cy="841" r="21" fill="var(--brand-white)" stroke="var(--brand-red)"/>
        <path d="M464 841 l7 7 l13 -14" fill="none" stroke="var(--brand-black)" stroke-width="3"/>
        <text x="514" y="848">HEFTY BILLS?</text>
      </g>
      <g class="option">
        <rect x="434" y="890" width="259" height="38" rx="12" fill="var(--brand-white)" stroke="var(--brand-red)" stroke-dasharray="3 2"/>
        <circle cx="474" cy="909" r="21" fill="var(--brand-white)" stroke="var(--brand-red)"/>
        <path d="M464 909 l7 7 l13 -14" fill="none" stroke="var(--brand-black)" stroke-width="3"/>
        <text x="514" y="906" font-size="18">BIRTH OF A</text>
        <text x="514" y="925" font-size="18">NEW CHILD?</text>
      </g>
    </g>

    <!-- solution -->
    <text class="slab solution" x="96" y="1023" font-size="50" font-weight="700" fill="var(--brand-white)" textLength="642" lengthAdjust="spacingAndGlyphs">IF SO, I HAVE THE SOLUTION.</text>

    <!-- contact bar -->
    <rect class="contact-bar" x="97" y="1043" width="632" height="33" fill="var(--brand-red)"/>
    <text class="serif-display" x="413" y="1068" text-anchor="middle" font-size="24" font-weight="700" fill="var(--brand-white)">Contact Yvonne Darcott today:</text>

    <!-- contact details -->
    <g class="contacts sans" font-weight="700" font-size="18" fill="var(--brand-white)">
      <g class="contact-phone">
        <rect x="99" y="1096" width="14" height="15" rx="2" fill="var(--brand-white)"/>
        <text x="130" y="1110">07419 604172</text>
      </g>
      <g class="contact-email">
        <rect x="301" y="1098" width="18" height="12" fill="none" stroke="var(--brand-white)" stroke-width="1.5"/>
        <path d="M301 1098 l9 7 l9 -7" fill="none" stroke="var(--brand-white)" stroke-width="1.5"/>
        <text x="329" y="1110">Yvonne@brightsteppath-example.co.uk</text>
      </g>
      <g class="contact-social-short">
        <circle cx="106" cy="1130" r="7" fill="var(--brand-white)"/>
        <text x="130" y="1136">@Bright_StepPath</text>
      </g>
      <g class="contact-social-page">
        <rect x="303" y="1123" width="14" height="14" fill="var(--brand-white)"/>
        <text x="329" y="1136">www.socialhub-example.com/yvonbrightsteppath</text>
      </g>
    </g>
  </svg>
</main>
</body>
</html>
```